Dog grooming business card
This is a business card for m dog grooming business like it say above.
In the priorities box below I will have the text that I want on the card.

Industry/Entity Type

Business

Colors

Designer to choose colors to be used in the design.

Requirements
Must have
• My logo and the insurance stamp must be on the card.

Text it must have :

Professional grooming services
Email: lunabrisk@mailvale.net
Text or call 1 705 318 6052
TWF certified/member
Pet first aid certified
Next appointment ___________________________________
Nice to have
• Greens to match my logo

```html
<!DOCTYPE html>
<html lang="en">
<head>
<meta charset="utf-8">
<title>Luna Brisk – Business Card</title>
<link href="https://fonts.googleapis.com/css2?family=Open+Sans:wght@400;600;700&display=swap" rel="stylesheet">
<style>
  :root {
    --backdrop: #2b2b2d;
    --card-white: #ffffff;
    --card-dark: #2a2729;
    --lime: #8dc63f;
    --ink: #231f20;
    --text-light: #f2f2f2;
    --text-muted: #bdbdbd;
    --badge-blue: #3d6fa8;
    --badge-fill: #e9eef5;
  }
  * { box-sizing: border-box; margin: 0; padding: 0; }
  html, body { width: 1200px; height: 800px; overflow: hidden; }
  body {
    background: var(--backdrop);
    font-family: "Open Sans", Arial, sans-serif;
    position: relative;
  }
  .card {
    position: absolute;
    top: 246px;
    width: 540px;
    height: 308px;
    border-radius: 4px;
    overflow: hidden;
    box-shadow: 0 12px 30px rgba(0,0,0,.45);
  }
  .card-front { left: 40px; background: var(--card-white); }
  .card-back { left: 620px; background: var(--card-dark); }

  /* front */
  .front-brand {
    position: absolute; inset: 0;
    display: flex; align-items: center; justify-content: center; gap: 18px;
  }
  .brand-dot {
    width: 58px; height: 58px; border-radius: 50%;
    background: var(--lime); flex: none;
  }
  .brand-name {
    font-weight: 700; font-size: 50px; color: var(--ink); letter-spacing: .5px;
    white-space: nowrap;
  }

  /* back */
  .swoosh { position: absolute; inset: 0; width: 100%; height: 100%; }
  .back-brand {
    position: absolute; left: 96px; top: 140px;
    display: flex; align-items: center; gap: 10px;
  }
  .back-brand .brand-dot { width: 30px; height: 30px; }
  .back-brand .brand-name { font-size: 26px; color: var(--lime); }
  .tagline {
    position: absolute; left: 92px; top: 184px;
    color: var(--text-light); font-size: 14px; white-space: nowrap;
  }
  .insurance-badge {
    position: absolute; left: 300px; top: 40px;
    width: 138px; height: 58px;
    border: 2px solid var(--badge-blue); border-radius: 8px;
    background: var(--badge-fill);
  }
  .contact {
    position: absolute; left: 345px; top: 112px;
    list-style: none; font-size: 12px; line-height: 1.55; white-space: nowrap;
  }
  .contact .person { color: var(--lime); font-weight: 700; font-size: 15px; line-height: 1.3; }
  .contact .role { color: var(--text-light); margin-bottom: 4px; }
  .contact .detail { color: var(--lime); }
  .contact .phone { color: var(--text-light); }
  .appointment {
    position: absolute; left: 180px; top: 262px;
    display: flex; align-items: flex-end; gap: 8px;
    color: var(--text-light); font-size: 12px; white-space: nowrap;
  }
  .appointment-line {
    width: 200px; border-bottom: 1px solid var(--text-muted); height: 14px;
  }
</style>
</head>
<body>
  <section class="card card-front" aria-label="Business card front">
    <div class="front-brand">
      <span class="brand-dot"></span>
      <span class="brand-name">Luna Brisk</span>
    </div>
  </section>

  <section class="card card-back" aria-label="Business card back">
    <svg class="swoosh" viewBox="0 0 540 308" preserveAspectRatio="none" aria-hidden="true">
      <path d="M420 0 H540 V240 C520 150 480 60 420 0 Z" fill="#8dc63f"/>
      <path d="M420 0 C480 60 520 150 540 240" fill="none" stroke="#ffffff" stroke-width="4"/>
      <path d="M0 40 C40 130 90 230 150 308 H0 Z" fill="#8dc63f"/>
      <path d="M0 40 C40 130 90 230 150 308" fill="none" stroke="#ffffff" stroke-width="4"/>
    </svg>
    <div class="back-brand">
      <span class="brand-dot"></span>
      <span class="brand-name">Luna Brisk</span>
    </div>
    <p class="tagline">Professional grooming services</p>
    <div class="insurance-badge" role="img" aria-label="Insurance protection badge"></div>
    <ul class="contact">
      <li class="person">Mara Delling</li>
      <li class="role">Manager</li>
      <li class="phone">1 705 318 6052</li>
      <li class="detail">lunabrisk@mailvale.net</li>
      <li class="detail">Pet first aid certified</li>
      <li class="detail">TWF certified/member</li>
    </ul>
    <p class="appointment">Next appointment <span class="appointment-line"></span></p>
  </section>
</body>
</html>
```